SaaS Early tech startup business card design

Unique design for experience ecommerce platform company. the business cards will be used by executive members. conformance with color code is required.

```html
<!DOCTYPE html>
<html lang="en">
<head>
<meta charset="utf-8">
<title>Velro business card</title>
<link href="https://fonts.googleapis.com/css2?family=Arimo:wght@400;700&display=swap" rel="stylesheet">
<style>
  :root {
    --page: #bdbdbd;
    --card-blue: #19668f;
    --teal: #1fb395;
    --deep: #0d3f57;
    --white: #ffffff;
  }
  * { box-sizing: border-box; margin: 0; padding: 0; }
  html, body {
    width: 1200px; height: 788px; overflow: hidden;
    background: var(--page);
    font-family: "Arimo", Arial, sans-serif;
  }
  .stage {
    width: 1200px; height: 788px;
    display: flex; align-items: center; justify-content: center; gap: 48px;
  }
  .card {
    position: relative;
    width: 540px; height: 310px;
    border-radius: 28px;
    background: var(--card-blue);
    overflow: hidden;
  }
  /* Front */
  .card-front .emblem {
    position: absolute;
    width: 330px; height: 330px;
    right: -70px; top: -80px;
    border-radius: 50%;
    background: var(--white);
    box-shadow: -5px 6px 0 0 var(--white), -9px 11px 0 0 var(--teal);
    display: flex; align-items: center; justify-content: center;
  }
  .brand-name {
    font-weight: 700;
    color: var(--teal);
    letter-spacing: -1px;
    line-height: 1;
  }
  .card-front .brand-name { font-size: 64px; margin: 50px 30px 0 0; }
  .details {
    position: absolute; left: 36px; bottom: 34px;
    color: var(--white);
    width: 250px;
  }
  .person-name {
    color: var(--teal); font-weight: 700; font-size: 20px; letter-spacing: 0.5px;
  }
  .person-role { font-size: 13px; margin-top: 3px; }
  .rule { height: 1px; background: var(--teal); margin: 10px 0; width: 220px; }
  .address { font-size: 12.5px; line-height: 1.35; }
  .contacts { list-style: none; font-size: 12.5px; line-height: 1.35; }
  .contacts li { display: flex; align-items: center; gap: 8px; }
  .contacts svg { width: 10px; height: 10px; fill: var(--teal); flex: none; }
  /* Back */
  .card-back { display: flex; align-items: center; justify-content: center; }
  .card-back .brand-name { font-size: 150px; color: var(--deep); letter-spacing: -4px; }
</style>
</head>
<body>
<main class="stage">
  <section class="card card-front">
    <div class="emblem"><span class="brand-name">velro</span></div>
    <div class="details">
      <h1 class="person-name">DANA WHITFIELD</h1>
      <p class="person-role">Owner/CEO</p>
      <div class="rule"></div>
      <p class="address">210 - 4820 Maple Ave<br>Burnaby, BC V5H2K1</p>
      <div class="rule"></div>
      <ul class="contacts">
        <li><svg viewBox="0 0 10 10"><path d="M2 0.5 3.6 2.6 2.7 3.6Q4 6 6.4 7.3L7.4 6.4 9.5 8 8.3 9.5Q3.5 8.5 0.5 1.7Z"/></svg>(604) 555 - 0142</li>
        <li><svg viewBox="0 0 10 10"><path d="M0.5 4Q5 0 9.5 4L8 5.2 6.8 4H3.2L2 5.2ZM1.5 6H8.5V9.5H1.5Z"/></svg>(604) 555 - 0187</li>
        <li><svg viewBox="0 0 10 10"><path d="M0.5 2H9.5V8H0.5ZM1.2 2.6 5 5.6 8.8 2.6" stroke="#19668f" stroke-width="0.8"/></svg>dana@velrohq.com</li>
        <li><svg viewBox="0 0 10 10"><circle cx="5" cy="5" r="4.5"/></svg>www.velrohq.com</li>
      </ul>
    </div>
  </section>
  <section class="card card-back">
    <span class="brand-name">velro</span>
  </section>
</main>
</body>
</html>
```